A clean crisp business card for a Landscape Construction company. Designed to be easy to read contact/ info and also be appealing/interesting, unlike a traditional business card.

Industry/Entity Type

Landscape Construction

Contact Information for Business Card

Company name : Brambleford Landscape Construction, phone number: (877) 62Vista, website:Bramblefordyards.example, Email, sales@bramblefordyards.example

Requirements
Nice to have
• Luxurious finishes/ details…. Icons or emblems next to contact info
Should not have
• Clipart or general pictures

```html
<!DOCTYPE html>
<html lang="en">
<head>
<meta charset="utf-8">
<title>Brambleford Landscape Construction – Business Card</title>
<link rel="stylesheet" href="https://fonts.googleapis.com/css2?family=Cinzel:wght@400;600&family=Open+Sans:wght@400;600&display=swap">
<style>
  :root {
    --page-bg: #e9e6e1;
    --card-white: #ffffff;
    --card-black: #121212;
    --brand-blue: #3f7fc4;
    --brand-green: #8cc63f;
    --ink-light: #f2f2f2;
    --shadow: rgba(0,0,0,0.22);
  }
  * { box-sizing: border-box; margin: 0; padding: 0; }
  html, body { width: 1200px; height: 913px; overflow: hidden; }
  body {
    background: var(--page-bg);
    display: flex;
    align-items: center;
    justify-content: center;
    gap: 40px;
    font-family: "Open Sans", sans-serif;
  }
  .card {
    width: 540px;
    height: 309px;
    border-radius: 4px;
    box-shadow: 0 10px 28px var(--shadow);
    position: relative;
    overflow: hidden;
  }
  .card--front {
    background: var(--card-white);
    display: flex;
    flex-direction: column;
    align-items: center;
    justify-content: center;
    gap: 26px;
  }
  .wordmark {
    display: flex;
    align-items: center;
    gap: 12px;
    font-family: "Cinzel", serif;
    font-weight: 600;
    color: var(--brand-blue);
    line-height: 1.05;
  }
  .wordmark__dot {
    width: 18px; height: 18px;
    border-radius: 50%;
    background: var(--brand-green);
    flex: none;
  }
  .wordmark__text { display: flex; flex-direction: column; }
  .wordmark__name { font-size: 34px; letter-spacing: 1px; }
  .wordmark__sub { font-size: 13px; letter-spacing: 3.4px; }
  .front__web {
    font-size: 14px;
    font-weight: 600;
    color: var(--brand-blue);
    letter-spacing: 0.3px;
  }
  .front__web span { color: var(--brand-green); }

  .card--back {
    background: linear-gradient(120deg, #0d0d0d 0%, #1d1d1d 55%, #0f0f0f 100%);
    display: flex;
    align-items: center;
    padding: 0 30px 0 32px;
  }
  .card--back .wordmark__name { font-size: 23px; }
  .card--back .wordmark__sub { font-size: 9px; letter-spacing: 2.3px; }
  .card--back .wordmark__dot { width: 13px; height: 13px; }
  .back__logo { flex: 0 0 230px; }
  .divider {
    width: 3px;
    height: 150px;
    margin: 0 20px 0 6px;
    display: flex;
    flex-direction: column;
  }
  .divider__green { flex: 1; background: var(--brand-green); width: 1px; margin: 0 auto; }
  .divider__blue { flex: 2; background: var(--brand-blue); }
  .contact { color: var(--ink-light); font-size: 11.5px; line-height: 1.55; }
  .contact__name {
    font-family: "Cinzel", serif;
    font-weight: 600;
    font-size: 19px;
    letter-spacing: 1px;
    color: var(--brand-blue);
    line-height: 1.1;
  }
  .contact__name span { color: var(--brand-green); }
  .contact__role { margin-bottom: 8px; }
  .contact__address { margin-bottom: 8px; }
  .contact__row { display: flex; align-items: center; gap: 7px; }
  .contact__row svg { width: 12px; height: 12px; flex: none; fill: var(--brand-green); }
</style>
</head>
<body>
  <section class="card card--front" aria-label="Card front">
    <div class="wordmark">
      <span class="wordmark__dot"></span>
      <div class="wordmark__text">
        <span class="wordmark__name">Brambleford</span>
        <span class="wordmark__sub">Landscape Construction</span>
      </div>
    </div>
    <p class="front__web">www.<span>Bramblefordyards</span>.example</p>
  </section>

  <section class="card card--back" aria-label="Card back">
    <div class="back__logo">
      <div class="wordmark">
        <span class="wordmark__dot"></span>
        <div class="wordmark__text">
          <span class="wordmark__name">Brambleford</span>
          <span class="wordmark__sub">Landscape Construction</span>
        </div>
      </div>
    </div>
    <div class="divider" aria-hidden="true">
      <span class="divider__green"></span>
      <span class="divider__blue"></span>
      <span class="divider__green"></span>
    </div>
    <div class="contact">
      <p class="contact__name">Evan <span>Hartley</span></p>
      <p class="contact__role">Director</p>
      <p class="contact__address">4130 Meadowcroft Rd.,<br>Suite 210, Larkfield, OH 45990</p>
      <p class="contact__row">
        <svg viewBox="0 0 24 24" aria-hidden="true"><path d="M6.6 10.8a15 15 0 0 0 6.6 6.6l2.2-2.2a1 1 0 0 1 1-.25 11.4 11.4 0 0 0 3.6.57 1 1 0 0 1 1 1V20a1 1 0 0 1-1 1A17 17 0 0 1 3 4a1 1 0 0 1 1-1h3.5a1 1 0 0 1 1 1c0 1.25.2 2.45.57 3.57a1 1 0 0 1-.25 1z"/></svg>
        (877) 62Vista
      </p>
      <p class="contact__row">
        <svg viewBox="0 0 24 24" aria-hidden="true"><path d="M2 5h20v14H2z M2 5l10 8 10-8" fill="none" stroke="#8cc63f" stroke-width="2.4"/></svg>
        sales@bramblefordyards.example
      </p>
      <p class="contact__row">
        <svg viewBox="0 0 24 24" aria-hidden="true"><circle cx="12" cy="12" r="10" fill="none" stroke="#8cc63f" stroke-width="2.4"/><path d="M2 12h20M12 2c3 3 3 17 0 20M12 2c-3 3-3 17 0 20" fill="none" stroke="#8cc63f" stroke-width="1.8"/></svg>
        www.bramblefordyards.example
      </p>
    </div>
  </section>
</body>
</html>
```